We’re a real estate firm that has landed a big builder in a neighboring state. Our branding needs...

We are a real estate firm who represents various builders along with doing resale here in Oregon. Our firm is growing to represent a big builder in Washington State and we’ll have another 40 brokers on our team. We need rebranding. As in, a new logo ( the house logo we have now looks cartoonish, hate it). We need new cards, something to really stand out. I’ve been thinking of using those NFC cards from ZEP or the ones with the seam color. I likely want two or three designs, a darker (as in a background color of black or grey) , a light one ( again I mean background color) and a credit card style (either plastic w an embossed name/number on front, or metal ). I’m thinking dark background for cc, or silver if it’s metal. That’s my thoughts, but you are the artists, so maybe you have an idea I haven’t considered. Our colors were black and red, but we don’t have to stick to that. Just nothing too busy. Oh, and we are typically representing the local, higher quality builders in our area (just below custom), but not national. Subdivisions are near the Kell Varney, Brisco, and Thornfield Crest sites. We are super excited, but without a lot of time to change the “look” of our brokerage. So I’ll be deciding and moving forward within 24 hours tops. Our name is Real Estate Summit Alliance ( we cant change the name because of timeline and business license) Thank you!

Industry/Entity Type

Real Estate

Contact Information for Business Card

The usual. Name of firm. Name of cardholder. Contact info.

Font styles to use
Serif
Sans Serif

Colors

Designer to choose colors to be used in the design.

Requirements
Must have
• A sleek or simple look. I included photos of cards with stylistic attributes we like. Thank you
Nice to have
• We really like the black backgrounds. With foil or embossed detail. We also like the black on black. Matte black card with raised shiny black detail. But still eye catching.
Should not have
• No ornate or busy looking style. We don’t want anything cluttered.

```html
<!DOCTYPE html>
<html lang="en">
<head>
<meta charset="utf-8">
<title>Real Estate Summit Alliance – Business Card</title>
<link rel="stylesheet" href="https://fonts.googleapis.com/css2?family=Lato:wght@400;700&display=swap">
<style>
  :root {
    --page-bg: #1c1c1d;
    --card-bg: #1f2022;
    --card-edge: #2a2b2e;
    --brand-red: #d42a2a;
    --text-light: #d9d9d9;
    --rule: #55575b;
    --pattern-a: #242527;
    --pattern-b: #2d2e31;
    --white: #ffffff;
  }
  html, body {
    margin: 0;
    padding: 0;
    width: 1200px;
    height: 1108px;
    overflow: hidden;
    background: var(--page-bg);
  }
  .canvas {
    position: relative;
    width: 1200px;
    height: 1108px;
  }
  .card {
    position: absolute;
    top: 204px;
    width: 400px;
    height: 700px;
    background: var(--card-bg);
    border-radius: 26px;
    box-shadow: 0 0 0 1px var(--card-edge);
    overflow: hidden;
  }
  .card--front { left: 160px; }
  .card--back { left: 640px; }

  /* Front: firm name in text font */
  .firm-name {
    position: absolute;
    top: 118px;
    left: 0;
    width: 100%;
    display: flex;
    flex-direction: column;
    align-items: center;
    gap: 18px;
  }
  .firm-name__mark {
    width: 56px;
    height: 56px;
    background: var(--brand-red);
  }
  .firm-name__text {
    margin: 0;
    width: 300px;
    text-align: center;
    font-family: "Lato", sans-serif;
    font-weight: 700;
    font-size: 28px;
    line-height: 34px;
    color: var(--brand-red);
  }

  .holder {
    position: absolute;
    top: 372px;
    left: 0;
    width: 100%;
    text-align: center;
    font-family: "Lato", sans-serif;
  }
  .holder__name {
    margin: 0;
    font-size: 24px;
    font-weight: 400;
    letter-spacing: 0.5px;
    color: var(--brand-red);
  }
  .holder__title {
    margin: 4px 0 0;
    font-size: 18px;
    color: var(--text-light);
  }
  .contact-rule {
    position: absolute;
    top: 452px;
    left: 50px;
    width: 300px;
    height: 28px;
  }
  .contact {
    position: absolute;
    top: 488px;
    left: 0;
    width: 100%;
    text-align: center;
    font-family: "Lato", sans-serif;
    font-size: 18px;
    line-height: 27px;
    color: var(--text-light);
  }
  .contact p, .address p { margin: 0; }
  .divider {
    position: absolute;
    top: 580px;
    left: 60px;
    width: 280px;
    height: 1px;
    background: var(--rule);
  }
  .address {
    position: absolute;
    top: 594px;
    left: 0;
    width: 100%;
    text-align: center;
    font-family: "Lato", sans-serif;
    font-size: 18px;
    line-height: 26px;
    color: var(--text-light);
  }

  /* Back */
  .pattern-field {
    position: absolute;
    top: 0;
    left: 0;
    width: 100%;
    height: 700px;
    background: linear-gradient(165deg, var(--pattern-b) 0%, var(--pattern-a) 70%, var(--card-bg) 100%);
  }
  .back-name {
    position: absolute;
    bottom: 90px;
    left: 0;
    width: 100%;
    text-align: center;
    margin: 0;
    font-family: "Lato", sans-serif;
    font-weight: 700;
    font-size: 30px;
    line-height: 36px;
    color: var(--white);
  }
</style>
</head>
<body>
<main class="canvas">

  <section class="card card--front" aria-label="Business card front">
    <div class="firm-name">
      <div class="firm-name__mark"></div>
      <p class="firm-name__text">Real Estate<br>Summit Alliance</p>
    </div>

    <div class="holder">
      <h1 class="holder__name">MARCUS HALE</h1>
      <p class="holder__title">Managing Director</p>
    </div>

    <svg class="contact-rule" viewBox="0 0 300 28" aria-hidden="true">
      <line x1="0" y1="14" x2="112" y2="14" stroke="var(--rule)" stroke-width="1"/>
      <line x1="188" y1="14" x2="300" y2="14" stroke="var(--rule)" stroke-width="1"/>
      <circle cx="126" cy="14" r="11" fill="var(--brand-red)"/>
      <path d="M121.5 9.5c1-1 2-.6 2.5.4l.8 1.6c.3.6 0 1.2-.5 1.6l-.6.5c.6 1.4 1.7 2.5 3 3.1l.5-.6c.4-.5 1-.7 1.6-.4l1.6.8c1 .5 1.3 1.5.4 2.4-2.6 2.6-11.4-6.3-9.3-9.4z" fill="var(--card-bg)"/>
      <circle cx="150" cy="14" r="11" fill="var(--brand-red)"/>
      <rect x="144" y="10" width="12" height="8" rx="1" fill="var(--card-bg)"/>
      <path d="M144 10.5l6 4.5 6-4.5" stroke="var(--brand-red)" stroke-width="1" fill="none"/>
      <circle cx="174" cy="14" r="11" fill="var(--brand-red)"/>
      <circle cx="174" cy="14" r="6" fill="none" stroke="var(--card-bg)" stroke-width="1.4"/>
      <ellipse cx="174" cy="14" rx="2.6" ry="6" fill="none" stroke="var(--card-bg)" stroke-width="1.2"/>
      <line x1="168" y1="14" x2="180" y2="14" stroke="var(--card-bg)" stroke-width="1.2"/>
    </svg>

    <div class="contact">
      <p>503 555 0142</p>
      <p>info@resummit.com</p>
      <p>www.resummitalliance.com</p>
    </div>

    <div class="divider"></div>

    <div class="address">
      <p>421 Cedar Ridge Way,</p>
      <p>Portland, OR 97205</p>
    </div>
  </section>

  <section class="card card--back" aria-label="Business card back">
    <div class="pattern-field" role="img" aria-label="Tone-on-tone repeating brand pattern in dark grey across the card back"></div>
    <p class="back-name">Real Estate<br>Summit Alliance</p>
  </section>

</main>
</body>
</html>
```